Tidy Hollow web design

I am after a web page design I can upload onto Site Build It! - which assists in building an ebusiness. I wish the site to have a vintage feel with a modern approach. I am fond of scroll or floral type motifs. As the web site will focus on home storage solutions, I would also like a practical feel too. I have a logo designed and ready to upload.

Target Market(s)

My target market is mature homeowners, particularly women who want stylish solutions to home storage.

Industry/Entity Type

Building

Requirements
Must have
• Logo to be prominent with co-ordinating background design. Navbar buttons to the left with similar background panel. far right column left available for associated links and advertisements.

```html
<!DOCTYPE html>
<html lang="en">
<head>
<meta charset="utf-8">
<title>Tidy Hollow — Home Storage</title>
<link href="https://fonts.googleapis.com/css2?family=Questrial&family=Quicksand:wght@400;500&family=Arimo:wght@400;700&family=Playfair+Display:wght@700&display=swap" rel="stylesheet">
<style>
:root{
  --backdrop-a:#dfe3d8;
  --backdrop-b:#c9d1bd;
  --page:#f4f4f2;
  --ink:#222;
  --muted:#555;
  --rule:#d4d4d0;
  --band:#e2e2df;
  --green:#64803c;
  --accent:#f08c00;
  --button:#4a4a4a;
  --bullet:#9aab5a;
  --white:#fff;
}
*{box-sizing:border-box;margin:0;padding:0}
html,body{width:1200px;height:978px;overflow:hidden}
body{font-family:"Arimo",Arial,sans-serif;color:var(--ink);position:relative}
.backdrop{position:absolute;inset:0;background:radial-gradient(ellipse at 20% 30%,#eef0ea 0%,var(--backdrop-a) 45%,var(--backdrop-b) 100%)}
.page{position:absolute;left:158px;top:0;width:884px;height:950px;background:var(--page);box-shadow:0 0 14px rgba(0,0,0,.18)}
.abs{position:absolute}

.brand{left:28px;top:30px;display:flex;align-items:center;gap:8px;font-family:"Questrial",sans-serif;font-size:28px;color:#3a4450}
.brand-dot{width:14px;height:14px;border-radius:50%;background:#3a4450}
.follow{left:734px;top:42px;display:flex;align-items:center;gap:10px;font-family:"Questrial",sans-serif;font-size:12px}
.social{width:19px;height:19px;border-radius:3px}
.social.one{background:#3b5a9a}
.social.two{background:#5fb8e0}

.nav{left:29px;top:94px;display:flex;font-family:"Questrial",sans-serif;font-size:12px;letter-spacing:.2px;white-space:nowrap}
.nav a{color:var(--ink);text-decoration:none}
.nav .sep{margin:0 11px}
.search{left:641px;top:90px;display:flex;height:22px}
.search-field{width:156px;border:1px solid #ccc;background:var(--white);font-size:10.5px;color:#555;padding:5px 10px}
.search-btn{width:62px;background:var(--button);color:var(--white);font-size:10.5px;padding:5px 0 0 8px;border-radius:0 3px 3px 0}

.hero{left:24px;top:130px;width:836px;height:268px;border:2px solid #ddd;border-radius:4px;overflow:hidden}
.hero-photo{position:absolute;inset:0;background:linear-gradient(90deg,#5f7f3b 0%,#6d8a45 60%,#7b9352 75%,#e9e8e4 76%,#f2f1ee 100%)}
.hero-floor{position:absolute;left:0;right:0;bottom:0;height:26px;background:linear-gradient(#dcdcd8,#f0f0ee)}
.hero-item{position:absolute;left:460px;top:84px;width:258px;height:176px;background:linear-gradient(#525a6a,#3f4656 80%,#b88a55 81%)}
.hero-title{position:absolute;left:50px;top:20px;font-family:"Quicksand",sans-serif;font-weight:500;color:var(--white);font-size:52px;line-height:46px}
.hero-title span{display:block}
.hero-title .l1{padding-left:36px}
.hero-title .l3{padding-left:32px}
.hero-copy{position:absolute;left:48px;top:184px;font-family:"Questrial",sans-serif;color:var(--white);font-size:15.5px;line-height:19px}
.hero-copy a{color:var(--accent);font-weight:700;text-decoration:none}

.side-nav{left:24px;top:424px;width:196px;font-family:"Questrial",sans-serif;font-size:12px}
.side-nav li{list-style:none;height:28.4px;line-height:28px;padding-left:21px;border-bottom:1px solid var(--rule)}
.side-nav li.current{background:var(--band);font-weight:700;padding-left:10px}
.side-nav li.current::before{content:"›";margin-right:8px;font-weight:700}

.box{border:1px solid var(--rule);background:var(--page);padding:12px 13px}
.cart{left:24px;top:691px;width:196px;height:89px}
.box h3{font-family:"Questrial",sans-serif;font-weight:400;font-size:14px;color:#333}
.box p{font-size:10px;line-height:16px;margin-top:6px;color:#333}
.cart-icon{position:absolute;right:10px;top:10px}
.subscribe{left:24px;top:794px;width:196px;height:89px}
.subscribe p{margin-top:2px;font-size:8.6px;white-space:nowrap}
.email{margin-top:8px;width:166px;height:20px;border:1px solid #888;background:var(--white);font-size:9.5px;padding:3px 6px}

.section-title{left:252px;top:431px;font-family:"Questrial",sans-serif;font-weight:700;font-size:13px;color:#444}
.product{width:140px;text-align:center;font-size:11px}
.product-photo{width:100px;height:110px;margin:0 auto;border-radius:4px}
.product h4{font-weight:400;margin-top:14px}
.product .price{font-weight:700;margin-top:6px}
.add{display:block;width:100px;height:20px;margin:7px auto 0;background:linear-gradient(#5a5a5a,#3c3c3c);color:var(--white);font-size:10px;line-height:20px;border-radius:2px}

.links{left:678px;top:415px;width:182px;height:147px;padding:11px 14px}
.links h3{font-size:13px;text-transform:uppercase;letter-spacing:.3px}
.links ul{margin-top:6px;list-style:none}
.links li{display:flex;align-items:center;gap:9px;font-family:"Questrial",sans-serif;font-size:12px;height:25px}
.links li::before{content:"";width:13px;height:13px;border-radius:50%;background:radial-gradient(circle at 40% 35%,#c8d58a,var(--bullet) 70%)}

.ad{left:678px;top:576px;width:182px;height:311px;border:1px solid var(--rule);background:var(--white);overflow:hidden}
.ad-title{position:absolute;left:8px;top:8px;font-family:"Playfair Display",serif;font-weight:700;font-size:34px;color:var(--green)}
.ad-sub{position:absolute;left:70px;top:52px;font-family:"Questrial",sans-serif;font-size:11.5px;color:var(--green)}
.ad-photo{position:absolute;left:0;right:0;top:74px;bottom:0;background:linear-gradient(#f4f2ee 0%,#f1ede6 40%,#e8642b 41%,#d9531f 85%,#eadfd6 86%)}

.footer{left:0;top:906px;width:884px;height:44px;background:var(--band);display:flex;justify-content:space-between;align-items:center;padding:0 22px;font-size:10.5px}
.footer .copy{font-weight:700;color:#333}
.footer nav a{color:var(--ink);text-decoration:none}
.footer nav .sep{color:#999;margin:0 5px}
</style>
</head>
<body>
<div class="backdrop" role="img" aria-label="Soft grey-green textured background with faint leafy scrolls"></div>

<div class="page">
  <div class="abs brand"><span class="brand-dot"></span>tidyhollow</div>

  <div class="abs follow">FOLLOW US: <span class="social one" aria-label="Social link"></span><span class="social two" aria-label="Social link"></span></div>

  <nav class="abs nav">
    <a href="#">HOME PAGE</a><span class="sep">|</span>
    <a href="#">NEW PRODUCTS</a><span class="sep">|</span>
    <a href="#">SPECIALS</a><span class="sep">|</span>
    <a href="#">ALL PRODUCTS</a><span class="sep">|</span>
    <a href="#">CONTACT US</a><span class="sep">|</span>
    <a href="#">FAQS</a>
  </nav>

  <div class="abs search">
    <div class="search-field">Search Our Products</div>
    <div class="search-btn">Search ▸</div>
  </div>

  <section class="abs hero">
    <div class="hero-photo" role="img" aria-label="Green wall with a slate grey storage sideboard on wooden legs and a white chair"></div>
    <div class="hero-floor"></div>
    <div class="hero-item" role="img" aria-label="Grey storage sideboard holding books"></div>
    <h1 class="hero-title"><span class="l1">Get</span><span>Organized</span><span class="l3">for Spring!</span></h1>
    <p class="hero-copy">tidyhollow has everything you need to<br>start your spring off on the right foot <a href="#">Read More</a></p>
  </section>

  <ul class="abs side-nav">
    <li class="current">FEATURED PRODUCTS</li>
    <li>SPECIALS</li>
    <li>BEDROOM</li>
    <li>FAMILY ROOM</li>
    <li>GARAGE</li>
    <li>HOME OFFICE</li>
    <li>KITCHEN</li>
    <li>LAUNDRY</li>
    <li>UTILITY</li>
  </ul>

  <div class="abs box cart">
    <h3>MY CART</h3>
    <svg class="cart-icon" width="26" height="20" viewBox="0 0 26 20" fill="none" stroke="#999" stroke-width="1.5"><path d="M1 2h4l3 11h13l3-8H7"/><circle cx="10" cy="17" r="1.6"/><circle cx="19" cy="17" r="1.6"/></svg>
    <p>You currently have no items in<br>your shopping cart</p>
  </div>

  <div class="abs box subscribe">
    <h3>Subscribe</h3>
    <p>Be Notified of upcoming News and Deals</p>
    <div class="email">Enter Your Email.</div>
  </div>

  <h2 class="abs section-title">FEATURED PRODUCTS</h2>

  <div class="abs product" style="left:235px;top:474px"><div class="product-photo" role="img" aria-label="Chrome mesh stacking shelves" style="background:linear-gradient(#d6d9dc,#9ea3a8)"></div><h4>Mesh Stacking Selves</h4><p class="price">$119.00</p><span class="add">Add to Cart</span></div>
  <div class="abs product" style="left:383px;top:474px"><div class="product-photo" role="img" aria-label="Cotton garment bags hanging" style="background:linear-gradient(#f1e9dc,#d8c8ae)"></div><h4>Cotton Garment Bags</h4><p class="price">$29.99</p><span class="add">Add to Cart</span></div>
  <div class="abs product" style="left:524px;top:474px"><div class="product-photo" role="img" aria-label="Rolling garment rack with clothes" style="background:linear-gradient(#ece8e2,#c9c2b6)"></div><h4>Garment Rack</h4><p class="price">$69.00</p><span class="add">Add to Cart</span></div>

  <div class="abs product" style="left:235px;top:683px"><div class="product-photo" role="img" aria-label="Grey zippered underbed bag" style="background:linear-gradient(#c9cbcd,#8f9295)"></div><h4>Underbed Bag</h4><p class="price">$14.99</p><span class="add">Add to Cart</span></div>
  <div class="abs product" style="left:383px;top:683px"><div class="product-photo" role="img" aria-label="Black handbag organizer" style="background:linear-gradient(#555,#1c1c1c)"></div><h4>Handbag Organizer</h4><p class="price">$11.99</p><span class="add">Add to Cart</span></div>
  <div class="abs product" style="left:524px;top:683px"><div class="product-photo" role="img" aria-label="Stacked storage bins" style="background:linear-gradient(#e3d3b4,#5a5856)"></div><h4>Storage Bin</h4><p class="price">$12.99</p><span class="add">Add to Cart</span></div>

  <aside class="abs box links">
    <h3>Associated Links</h3>
    <ul>
      <li>tidyhollow one</li>
      <li>tidyhollow two</li>
      <li>tidyhollow three</li>
      <li>tidyhollow four</li>
    </ul>
  </aside>

  <aside class="abs ad">
    <div class="ad-title">40% OFF</div>
    <div class="ad-sub">SELECTED ITEMS</div>
    <div class="ad-photo" role="img" aria-label="Orange open shelving unit with a vase of flowers"></div>
  </aside>

  <footer class="abs footer">
    <span class="copy">© 2011 Tidy Hollow. All Rights Reserved.</span>
    <nav><a href="#">Bedroom</a><span class="sep">|</span><a href="#">Family Room</a><span class="sep">|</span><a href="#">Garage</a><span class="sep">|</span><a href="#">Home Office</a><span class="sep">|</span><a href="#">Kitchen</a><span class="sep">|</span><a href="#">Laundry</a><span class="sep">|</span><a href="#">Utility</a><span class="sep">|</span><a href="#">Follow</a></nav>
  </footer>
</div>
</body>
</html>
```